Coastline Premier Retreats Business Card Design

Design a business card for Coastline Premier Retreats. Look at the website for colors and reference. Card should have logo, name, title, office number, mobile number, email, URL and a tagline like, "Luxury Hotel & Resort Email Marketing" (This might change).

https://www.coastlinepremierretreats.example

The rest I will leave up to your imagination.

Contact Information for Business Card

Logo, name, title, office number, mobile number, email, URL and a tagline like, "Luxury Hotel & Resort Email Marketing" (This might change).

```html
<!DOCTYPE html>
<html lang="en">
<head>
<meta charset="utf-8">
<title>Coastline Premier Retreats — Business Card</title>
<link href="https://fonts.googleapis.com/css2?family=Arimo:wght@400;700&display=swap" rel="stylesheet">
<style>
  :root {
    --orange: #e36c0a;
    --white: #f7f7f7;
    --ink: #111111;
    --gold: #eac55e;
    --backdrop: #c9c9c9;
    --card-w: 520px;
    --card-h: 297px;
  }
  * { box-sizing: border-box; margin: 0; padding: 0; }
  html, body {
    width: 1200px; height: 800px; overflow: hidden;
    background: var(--backdrop);
    font-family: "Arimo", Arial, sans-serif;
  }
  .canvas { position: relative; width: 1200px; height: 800px; }

  .card {
    position: absolute;
    width: var(--card-w); height: var(--card-h);
    border-radius: 16px; overflow: hidden;
    box-shadow: 0 10px 28px rgba(0,0,0,.22);
  }
  .card--front { left: 50px; top: 120px; background: var(--white); }
  .card--back { left: 630px; top: 383px; background: var(--orange); }

  .card__shapes { position: absolute; inset: 0; }

  .brand {
    position: absolute;
    display: flex; align-items: center; gap: 8px;
    font-weight: 700; text-transform: uppercase; letter-spacing: .04em;
  }
  .brand__square { width: 10px; height: 10px; flex: none; background: var(--orange); }
  .brand--front {
    left: 30px; top: 130px; width: 200px;
    font-size: 15px; line-height: 1.2; color: var(--ink);
  }
  .brand--back {
    left: 0; right: 0; top: 128px; justify-content: center;
    font-size: 26px; color: var(--gold);
  }
  .brand--back .brand__square { width: 16px; height: 16px; background: var(--gold); }

  .contact {
    position: absolute; right: 22px; top: 26px; width: 210px;
    text-align: right; color: var(--white);
  }
  .contact__name { font-size: 19px; font-weight: 700; color: var(--ink); line-height: 1.1; }
  .contact__title { font-size: 11px; margin-bottom: 14px; }
  .contact__line {
    display: flex; justify-content: flex-end; align-items: center; gap: 6px;
    font-size: 10.5px; line-height: 15px; white-space: nowrap;
  }
  .contact__icon { width: 10px; height: 10px; flex: none; }
  .contact__tagline { margin-top: 16px; font-size: 11px; white-space: nowrap; }
</style>
</head>
<body>
<main class="canvas">

  <section class="card card--front" aria-label="Card front">
    <svg class="card__shapes" width="520" height="297" viewBox="0 0 520 297">
      <polygon points="270,0 520,0 520,297 332,297" fill="var(--orange)"/>
      <polygon points="258,0 266,0 328,297 316,297" fill="var(--ink)"/>
    </svg>

    <div class="brand brand--front">
      <span class="brand__square"></span>
      <span class="brand__name">Coastline Premier Retreats</span>
    </div>

    <div class="contact">
      <p class="contact__name">Daniel Brooks</p>
      <p class="contact__title">President</p>

      <p class="contact__line">555.014.2200
        <svg class="contact__icon" viewBox="0 0 10 10"><path d="M2 1 L4 1 L4.6 3 L3.4 3.8 Q4.4 5.8 6.2 6.6 L7 5.4 L9 6 L9 8 Q5 9 2 5 Q1 3 2 1Z" fill="var(--ink)"/></svg>
      </p>
      <p class="contact__line">555.014.2201
        <svg class="contact__icon" viewBox="0 0 10 10"><rect x="2.5" y="0.5" width="5" height="9" rx="1" fill="none" stroke="var(--ink)" stroke-width="1.2"/></svg>
      </p>
      <p class="contact__line">info@coastlinepremierretreats.example
        <svg class="contact__icon" viewBox="0 0 10 10"><rect x="0.5" y="2" width="9" height="6.5" fill="var(--ink)"/><path d="M0.5 2 L5 5.5 L9.5 2" fill="none" stroke="var(--orange)" stroke-width=".9"/></svg>
      </p>
      <p class="contact__line">www.coastlinepremierretreats.example
        <svg class="contact__icon" viewBox="0 0 10 10"><circle cx="5" cy="5" r="4.5" fill="var(--ink)"/><path d="M0.5 5 H9.5 M5 0.5 V9.5" stroke="var(--orange)" stroke-width=".8"/></svg>
      </p>

      <p class="contact__tagline">Luxury Hotel &amp; Resort Email Marketing</p>
    </div>
  </section>

  <section class="card card--back" aria-label="Card back">
    <div class="brand brand--back">
      <span class="brand__square"></span>
      <span class="brand__name">Coastline Premier Retreats</span>
    </div>
  </section>

</main>
</body>
</html>
```